Web Design for an Innovative Life Science Marketplace

IMPORTANT:
The software is called CS-Cart. It has capabilities and limitations with design features in the software. There is a certain framework that needs to be followed. It is PHP and Linux. It may require add-ons for your design, so please be specific with what is required. It’s preferred the designer has CS-Cart knowledge/experience.

Key Requirements
1. I’d like the design to include an implemented/recommended CS-Cart theme that is consistent with our branding (see the marketing collateral and logo).
2. I then need the additional design changes to that theme to create the below web pages.
3. All designs should be consistent with our branding. All pictures should either be computer generated (clip art-like) or pictures of happy patients. What is a happy patient? Close up photo of someone healthy, happy, and experiencing/enjoying life. Not someone in a hospital or getting care. Please see examples already on the site.

Please see the attached Web Design details in the word document. That document is important to complete the design.

```html
<!DOCTYPE html>
<html lang="en">
<head>
<meta charset="utf-8">
<title>VitaLink – About</title>
<link href="https://fonts.googleapis.com/css2?family=Montserrat:wght@400;600;700&family=Open+Sans:wght@400;600&display=swap" rel="stylesheet">
<style>
:root{
  --green:#7dc242;
  --green-dark:#5fa52c;
  --teal:#1f9e8f;
  --ink:#333;
  --muted:#777;
  --dark:#2b2b2b;
  --darker:#1d1d1d;
  --light:#f4f4f4;
  --white:#fff;
}
*{box-sizing:border-box;margin:0;padding:0}
html,body{width:804px;height:1200px;overflow:hidden;background:var(--white)}
body{font-family:"Open Sans",Arial,sans-serif;color:var(--ink);font-size:9px;position:relative}
.topbar{height:21px;background:var(--darker);color:#ccc;font-size:7px;display:flex;align-items:center;padding:0 110px;gap:18px}
.topbar .right{margin-left:auto}
.header{height:79px;display:flex;align-items:center;padding:0 110px}
.brand{display:flex;align-items:center;gap:6px;font-family:"Montserrat",sans-serif;font-weight:700;font-size:15px;color:var(--green-dark)}
.brand .dot{width:26px;height:26px;border-radius:50%;background:var(--green)}
.cart{margin-left:auto;display:flex;align-items:center;gap:8px}
.cart .box{width:26px;height:22px;background:var(--green);border-radius:3px}
.cart .label{font-size:8px;line-height:1.3}
.cart .label b{display:block;font-size:9px}
.search{margin-left:20px;width:110px;height:20px;border:1px solid #ccc;border-radius:10px;font-size:7px;color:#999;padding:5px 9px}
.nav{height:24px;background:var(--green);display:flex;padding:0 110px}
.nav a{color:var(--white);text-decoration:none;font-size:7px;font-weight:600;padding:0 14px;line-height:24px}
.nav a.active{background:var(--green-dark)}
.hero{height:211px;position:relative;background:linear-gradient(90deg,#b7d98a 0%,#dbe9c2 45%,#e9d3c1 75%,#cfe3b0 100%)}
.hero h1{position:absolute;left:54px;top:80px;font-family:"Montserrat",sans-serif;font-weight:700;font-size:46px;color:var(--white);letter-spacing:1px}
.hero h1 span{color:var(--green-dark);font-size:62px}
.about{display:flex;gap:28px;padding:25px 110px 0 94px;height:322px}
.about .photo{width:241px;height:242px;flex:none;background:linear-gradient(135deg,#e3c7ae,#c59a7d 60%,#d9e6c8)}
.about h2{font-family:"Montserrat",sans-serif;font-size:20px;font-weight:700;margin:12px 0 12px}
.about h2 span{font-size:30px}
.about p{font-size:7.5px;line-height:1.6;color:var(--muted);margin-bottom:10px}
.partners{text-align:center;height:173px}
.section-title{font-family:"Montserrat",sans-serif;font-weight:700;font-size:24px;color:var(--ink);display:inline-flex;align-items:center;gap:10px;margin-top:20px}
.section-title::before,.section-title::after{content:"";width:70px;height:1px;background:#bbb}
.section-title span{color:var(--green);font-size:34px}
.logos{display:flex;justify-content:center;align-items:center;gap:28px;margin-top:20px}
.logos .arrow{width:14px;height:14px;color:#999}
.logos .badge{width:100px;height:42px;background:var(--light);border:1px solid #e2e2e2;border-radius:3px}
.contact-band{height:108px;background:var(--green);display:flex;justify-content:space-around;align-items:center;padding:0 90px}
.contact-band .item{display:flex;align-items:center;gap:10px;color:var(--white);font-size:10px;font-weight:600}
.contact-band .ring{width:40px;height:40px;border:2px solid var(--white);border-radius:50%;display:flex;align-items:center;justify-content:center}
.footer-main{height:242px;background:var(--dark);color:#ccc;padding-top:18px}
.connect{text-align:center}
.connect h3{font-family:"Montserrat",sans-serif;color:var(--white);font-size:14px;font-weight:700}
.connect h3 span{color:var(--green);font-size:20px}
.socials{display:flex;justify-content:center;gap:5px;margin-top:8px}
.socials i{width:16px;height:16px;border:1px solid #999;display:block}
.cols{display:flex;gap:50px;padding:18px 110px 0}
.col{flex:1}
.col h4{font-family:"Montserrat",sans-serif;color:var(--white);font-size:13px;margin-bottom:10px}
.col h4 span{color:var(--green);font-size:19px}
.field{height:18px;background:var(--white);border-radius:2px;font-size:7px;color:#999;padding:4px 6px;margin-bottom:6px}
.btn{display:inline-block;background:var(--teal);color:var(--white);font-size:7px;padding:4px 12px;border-radius:10px}
.tweet{font-size:7px;line-height:1.5;margin-bottom:8px}
.tweet b{color:var(--green)}
.map{height:84px;background:linear-gradient(135deg,#d7dde3,#b9c6d2)}
.bottombar{height:20px;background:var(--darker);color:#999;font-size:6.5px;display:flex;align-items:center;padding:0 110px;gap:12px}
.bottombar .copy{margin-left:auto}
</style>
</head>
<body>
<div class="topbar"><span>hello@vitalink.com</span><span>555-014-2290</span><span class="right">My Account · Login</span></div>
<header class="header">
  <div class="brand"><span class="dot"></span>VITALINK</div>
  <div class="cart"><span class="box"></span><div class="label"><b>SHOPPING CART</b>0 items – $0.00</div></div>
  <div class="search">Search products…</div>
</header>
<nav class="nav"><a class="active">HOME</a><a>ABOUT US</a><a>HOW IT WORKS</a><a>OUR PLATFORM</a><a>BENEFITS</a><a>CONTACT US</a></nav>
<section class="hero" role="img" aria-label="Smiling healthy person relaxing outdoors on green foliage">
  <h1><span>A</span>BOUT</h1>
</section>
<section class="about">
  <div class="photo" role="img" aria-label="Close-up portrait of a happy, healthy person"></div>
  <div>
    <h2><span>A</span>BOUT VITALINK</h2>
    <p>We are a trusted online marketplace connecting life science researchers, suppliers and patients. Our platform makes it simple to find, compare and order quality products, while every partner is carefully reviewed for reliability and service.</p>
    <p>Our mission is to speed discovery by removing friction from ordering, payment and delivery. We support small labs and large institutions alike with clear pricing, secure checkout and responsive help whenever it is needed.</p>
    <p>We believe healthier lives begin with better access. By bringing suppliers, clinicians and innovators together in one place, we help new treatments reach the people who need them faster, and we keep improving our tools with feedback from the community we serve every day.</p>
  </div>
</section>
<section class="partners">
  <h2 class="section-title"><span>O</span>UR PARTNERS</h2>
  <div class="logos">
    <svg class="arrow" viewBox="0 0 14 14"><path d="M9 2 4 7l5 5" fill="none" stroke="currentColor" stroke-width="2"/></svg>
    <div class="badge"></div><div class="badge"></div><div class="badge"></div><div class="badge"></div><div class="badge"></div>
    <svg class="arrow" viewBox="0 0 14 14"><path d="m5 2 5 5-5 5" fill="none" stroke="currentColor" stroke-width="2"/></svg>
  </div>
</section>
<section class="contact-band">
  <div class="item"><span class="ring"><svg width="18" height="18" viewBox="0 0 24 24"><path d="M6.6 10.8a15 15 0 0 0 6.6 6.6l2.2-2.2c.3-.3.7-.4 1-.2 1.1.4 2.3.6 3.6.6.6 0 1 .4 1 1V20c0 .6-.4 1-1 1A17 17 0 0 1 3 4c0-.6.4-1 1-1h3.5c.6 0 1 .4 1 1 0 1.3.2 2.5.6 3.6.1.3 0 .7-.2 1z" fill="#fff"/></svg></span>555-014-2290</div>
  <div class="item"><span class="ring"><svg width="18" height="18" viewBox="0 0 24 24"><rect x="3" y="5" width="18" height="14" rx="1" fill="none" stroke="#fff" stroke-width="2"/><path d="m3 6 9 7 9-7" fill="none" stroke="#fff" stroke-width="2"/></svg></span>hello@vitalink.com</div>
  <div class="item"><span class="ring"><svg width="18" height="18" viewBox="0 0 24 24"><path d="M12 2a7 7 0 0 0-7 7c0 5 7 13 7 13s7-8 7-13a7 7 0 0 0-7-7zm0 9.5A2.5 2.5 0 1 1 12 6.5a2.5 2.5 0 0 1 0 5z" fill="#fff"/></svg></span>48 Orchard Lane, NY</div>
</section>
<footer class="footer-main">
  <div class="connect"><h3><span>C</span>ONNECT WITH US</h3><div class="socials"><i></i><i></i><i></i></div></div>
  <div class="cols">
    <div class="col"><h4><span>N</span>EWSLETTER</h4><div class="field">Enter your email here</div><span class="btn">SUBSCRIBE</span></div>
    <div class="col"><h4><span>U</span>PDATES</h4>
      <p class="tweet"><b>@vitalink</b> New partner suppliers added this week, browse the latest catalog.</p>
      <p class="tweet"><b>@vitalink</b> Faster checkout is now live for all research accounts.</p>
    </div>
    <div class="col"><h4><span>L</span>OCATION</h4><div class="map" role="img" aria-label="Street map showing the office location"></div></div>
  </div>
</footer>
<div class="bottombar"><span>HOME</span><span>ABOUT US</span><span>HOW IT WORKS</span><span>OUR PLATFORM</span><span>BENEFITS</span><span>CONTACT US</span><span class="copy">© VITALINK. ALL RIGHTS RESERVED</span></div>
</body>
</html>
```